Fresh, modern, fun business card for pediatric dental practice

Need a business card for fresh, modern, fun pediatric dental practice

Clean look that matches our website's font and colors

We prefer the look of curved corners on business cards

Target Market(s)

parents (mothers) of young children, professionals, mid-high class

Industry/Entity Type

Dental

Contact Information for Business Card

Maplebrook Pediatric Dentistry
482 Quarry Lane
Suite 517
Harwick Springs, ID 83999
208.555.0193
www.maplebrookkidsdental.example

Mei-Ran Tsai, DMD
Corinne Walbeck, DMD
(we are working on our email address, but we would like that on the card as well)

Font styles to use
Sans Serif

Requirements
Must have
• All info; we would also like to make cards for individual staff members
• colors from our website and color palatte, attatched
• use same font and design as website for branding
Nice to have
• clean, simple card that has a pop of color
• we would like to see a few designs with our tag line "where smiles get brighter"
• we are not sure if we want to have it on there or not
• we would like to see a few designs incorporating the ribbon graphic on our website where the word WELCOME is

```html
<!DOCTYPE html>
<html lang="en">
<head>
<meta charset="utf-8">
<title>Maplebrook Pediatric Dentistry – Business Card</title>
<link rel="stylesheet" href="https://fonts.googleapis.com/css2?family=Lato:wght@400;700&display=swap">
<style>
  :root {
    --magenta: #d6299d;
    --magenta-deep: #b81c86;
    --magenta-light: #e04fb3;
    --sun-yellow: #f2bd2f;
    --ink-grey: #555457;
    --card-white: #f7f7f7;
    --backdrop: #e4e3e6;
  }
  * { box-sizing: border-box; margin: 0; padding: 0; }
  html, body { width: 1200px; height: 900px; overflow: hidden; }
  body {
    background: var(--backdrop);
    font-family: "Lato", Arial, sans-serif;
    position: relative;
  }
  .card {
    position: absolute;
    left: 340px;
    width: 520px;
    height: 297px;
    border-radius: 18px;
    overflow: hidden;
    box-shadow: 0 10px 28px rgba(0,0,0,.18);
  }
  .card--front { top: 110px; background: var(--card-white); }
  .card--back { top: 490px; }

  /* front */
  .name-ribbon {
    position: absolute;
    left: 0; top: 34px;
    width: 330px; height: 44px;
  }
  .name-ribbon svg { position: absolute; inset: 0; }
  .name-ribbon__text {
    position: relative;
    line-height: 44px;
    padding-left: 64px;
    color: #fff;
    font-size: 22px;
    font-weight: 400;
    white-space: nowrap;
  }
  .name-ribbon__title { color: var(--sun-yellow); }

  .contact-list {
    position: absolute;
    left: 28px; top: 120px;
    list-style: none;
  }
  .contact-list li {
    display: flex; align-items: center;
    height: 22px;
    font-size: 12.5px;
    color: var(--ink-grey);
    white-space: nowrap;
  }
  .contact-icon { width: 15px; height: 15px; margin-right: 9px; flex: none; }

  .practice-name {
    position: absolute;
    right: 36px; top: 132px;
    display: flex; align-items: center; gap: 8px;
    font-size: 28px;
    font-weight: 700;
    color: var(--sun-yellow);
    white-space: nowrap;
  }
  .practice-name__dot {
    width: 16px; height: 16px; border-radius: 50%;
    background: var(--sun-yellow);
  }
  .address {
    position: absolute;
    right: 36px; bottom: 26px;
    text-align: right;
    font-style: normal;
    font-size: 13px;
    line-height: 1.45;
    color: var(--ink-grey);
    white-space: nowrap;
  }
  .address__org { color: var(--magenta); font-weight: 700; }

  /* back */
  .back-pattern {
    position: absolute; inset: 0;
    background: radial-gradient(circle at 35% 30%, var(--magenta-light), var(--magenta) 55%, var(--magenta-deep));
  }
  .back-name {
    position: absolute;
    inset: 0;
    display: flex; align-items: center; justify-content: center;
    color: rgba(255,255,255,.85);
    font-size: 38px;
    font-weight: 700;
    letter-spacing: 1px;
  }
</style>
</head>
<body>
  <section class="card card--front" aria-label="Business card front">
    <div class="name-ribbon">
      <svg width="330" height="44" viewBox="0 0 330 44" aria-hidden="true">
        <polygon points="0,0 330,0 312,22 330,44 0,44" fill="var(--magenta)"/>
      </svg>
      <p class="name-ribbon__text">Mei-Ran Tsai, <span class="name-ribbon__title">DMD</span></p>
    </div>

    <ul class="contact-list">
      <li>
        <svg class="contact-icon" viewBox="0 0 16 16" aria-hidden="true"><circle cx="8" cy="8" r="8" fill="var(--magenta)"/><path d="M5.2 4.2l1.4-.2.7 1.8-.9.7c.5 1.1 1.3 1.9 2.3 2.4l.7-.9 1.8.7-.2 1.4c-3.1.2-6-2.7-5.8-5.9z" fill="#fff"/></svg>
        208.555.0193
      </li>
      <li>
        <svg class="contact-icon" viewBox="0 0 16 16" aria-hidden="true"><circle cx="8" cy="8" r="8" fill="var(--magenta)"/><rect x="4" y="5.2" width="8" height="5.6" rx=".6" fill="#fff"/><path d="M4.3 5.6L8 8.4l3.7-2.8" stroke="var(--magenta)" stroke-width=".9" fill="none"/></svg>
        info@maplebrookkidsdental.example
      </li>
      <li>
        <svg class="contact-icon" viewBox="0 0 16 16" aria-hidden="true"><circle cx="8" cy="8" r="8" fill="var(--magenta)"/><circle cx="8" cy="8" r="4" fill="none" stroke="#fff" stroke-width="1"/><ellipse cx="8" cy="8" rx="1.7" ry="4" fill="none" stroke="#fff" stroke-width=".9"/><line x1="4" y1="8" x2="12" y2="8" stroke="#fff" stroke-width=".9"/></svg>
        www.maplebrookkidsdental.example
      </li>
    </ul>

    <p class="practice-name"><span class="practice-name__dot" aria-hidden="true"></span>Maplebrook</p>

    <address class="address">
      <span class="address__org">Maplebrook Pediatric Dentistry</span><br>
      482 Quarry Lane, Suite 517<br>
      Harwick Springs, ID 83999
    </address>
  </section>

  <section class="card card--back" aria-label="Business card back">
    <div class="back-pattern" role="img" aria-label="Repeating pattern of small orange spiral suns on magenta"></div>
    <p class="back-name">Maplebrook</p>
  </section>
</body>
</html>
```